Visitenkarten-Design für Pflegedienst
Zielgruppe
Pflegedienst
Aufgabenstellung
Siehe Beispielvisitenkarte. Es soll so ähnlich designt werden mit hochwertigem Papier. Die Angaben darauf sind auch schon korrekt.

```html
<!DOCTYPE html>
<html lang="de">
<head>
<meta charset="utf-8">
<title>Visitenkarte Atemweg18 GmbH</title>
<link href="https://fonts.googleapis.com/css2?family=Barlow+Semi+Condensed:wght@300;400;600&display=swap" rel="stylesheet">
<style>
  :root {
    --navy: #1b4276;
    --red: #c4161c;
    --paper: #ffffff;
    --page: #ffffff;
    --edge: #bfc3c8;
    --photo-light: #f2f2f2;
    --photo-mid: #e2e2e2;
  }
  * { box-sizing: border-box; margin: 0; padding: 0; }
  html, body { width: 1200px; height: 1200px; overflow: hidden; background: var(--page); }
  body { font-family: "Barlow Semi Condensed", "Arial Narrow", sans-serif; color: var(--navy); position: relative; }

  .card {
    position: absolute;
    left: 190px;
    width: 820px;
    height: 538px;
    background: var(--paper);
    border: 1px solid var(--edge);
    box-shadow: 2px 3px 6px rgba(0,0,0,0.18);
    overflow: hidden;
  }
  .card--front { top: 40px; }
  .card--back { top: 620px; }

  .card__band {
    position: absolute;
    left: 0; right: 0;
    top: 27px;
    height: 90px;
    background: var(--navy);
    color: #fff;
    display: flex;
    align-items: center;
    padding-left: 53px;
  }
  .card__name {
    font-weight: 300;
    font-size: 42px;
    letter-spacing: 3.5px;
  }
  .card__url {
    font-weight: 300;
    font-size: 40px;
    letter-spacing: 1px;
  }

  .contact {
    position: absolute;
    left: 53px;
    top: 134px;
    font-size: 24px;
    font-weight: 300;
    line-height: 33px;
    letter-spacing: 0.6px;
  }
  .contact__role { font-weight: 400; margin-bottom: 33px; }
  .contact__role strong { font-weight: 600; }
  .contact__block { margin-bottom: 33px; }
  .contact__mail { font-weight: 600; }

  .portrait {
    position: absolute;
    left: 470px;
    right: 0;
    top: 117px;
    bottom: 0;
    background: radial-gradient(ellipse at 50% 40%, var(--photo-light) 0%, var(--photo-mid) 100%);
  }

  .brand {
    position: absolute;
    left: 95px;
    top: 188px;
    display: flex;
    align-items: center;
  }
  .brand__dot {
    width: 96px; height: 96px;
    border-radius: 50%;
    background: var(--red);
    margin-right: 24px;
  }
  .brand__divider {
    width: 2px;
    height: 172px;
    background: var(--navy);
    margin-right: 24px;
  }
  .brand__name {
    font-size: 52px;
    font-weight: 400;
    line-height: 1;
    color: var(--navy);
    letter-spacing: 1px;
  }
  .brand__tagline {
    font-size: 26px;
    font-weight: 400;
    color: var(--red);
    margin-top: 4px;
    letter-spacing: 0.5px;
  }
</style>
</head>
<body>

<section class="card card--front">
  <div class="card__band"><h1 class="card__name">MAREK STOJANOVIĆ LL.M.</h1></div>
  <div class="contact">
    <p class="contact__role"><strong>Wirtschaftsjurist</strong> | Geschäftsführer</p>
    <p class="contact__block">Atemweg18 GmbH<br>Lindenhofer Str. 12<br>70123 Musterstadt</p>
    <p class="contact__block">M.+49 152 40418832<br>T. +49 7041 5528100<br>F. +49 7041 5528102</p>
    <p class="contact__mail">ms@atemweg18.de</p>
  </div>
  <div class="portrait" role="img" aria-label="Porträtfoto des Geschäftsführers im weißen Hemd vor hellem Hintergrund"></div>
</section>

<section class="card card--back">
  <div class="card__band"><p class="card__url">www.atemweg18.de</p></div>
  <div class="brand">
    <span class="brand__dot"></span>
    <span class="brand__divider"></span>
    <div>
      <p class="brand__name">ATEMWEG18 GMBH</p>
      <p class="brand__tagline">AUSSERKLINISCHE INTENSIVPFLEGE</p>
    </div>
  </div>
</section>

</body>
</html>
```